New stationary design for online film company

We need some new stationary to fit with our new logo. The stationary should be professional, clean and simple.
We need designs for a full set of business stationary.
We need - letterhead, envelopes, invoices, proposals, coverslip/note and cover page

Industry/Entity Type

Business

```html
<!DOCTYPE html>
<html lang="en">
<head>
<meta charset="utf-8">
<title>Lumenreel Stationery Set</title>
<link href="https://fonts.googleapis.com/css2?family=Open+Sans:wght@400;600;700&display=swap" rel="stylesheet">
<style>
  :root {
    --navy: #0f4870;
    --sky: #6aa2bd;
    --paper: #ffffff;
    --paper-shade: #eef0f3;
    --mark-faint: #dcdee6;
    --ink: #4a4f57;
    --backdrop: #c7844e;
    --label: #ffffff;
  }
  * { box-sizing: border-box; margin: 0; padding: 0; }
  html, body { width: 1200px; height: 490px; overflow: hidden; }
  body {
    position: relative;
    background: var(--backdrop);
    font-family: "Open Sans", Arial, sans-serif;
    color: var(--ink);
  }
  .sheet {
    position: absolute;
    background: linear-gradient(160deg, var(--paper) 55%, var(--paper-shade));
    box-shadow: 0 1px 4px rgba(0,0,0,.25);
    overflow: hidden;
  }
  .brand {
    display: flex; align-items: center; gap: 6px;
    font-weight: 600; color: var(--navy); letter-spacing: -.3px;
    position: absolute;
  }
  .brand-dot { border-radius: 50%; background: var(--navy); flex: none; }
  .faint-circle { position: absolute; border-radius: 50%; background: var(--mark-faint); }
  .small { font-size: 5.4px; line-height: 1.55; color: var(--ink); position: absolute; }
  .small .ico { color: var(--navy); margin-right: 3px; }

  /* Letterheads */
  .letterhead { width: 332px; height: 430px; top: 18px; }
  .letterhead--one { left: 6px; }
  .letterhead--two { left: 370px; }
  .letterhead .brand { font-size: 21px; top: 20px; }
  .letterhead--one .brand { left: 50%; transform: translateX(-50%); }
  .letterhead--two .brand { left: 10px; }
  .letterhead--one .faint-circle { width: 260px; height: 260px; left: -40px; top: 250px; }
  .letterhead--two .faint-circle { width: 56px; height: 56px; right: 4px; bottom: 22px; }
  .footer-line { bottom: 8px; left: 0; right: 0; text-align: center; white-space: nowrap; }
  .footer-line span + span::before { content: "|"; margin: 0 4px; color: #aaa; }
  .address-block { top: 29px; left: 256px; padding-left: 4px; border-left: 1px solid #bbb; }
  .contact-stack { left: 10px; bottom: 11px; }

  .option-label {
    position: absolute; top: 462px; font-size: 22px; color: var(--label); font-weight: 400;
  }

  /* Envelopes */
  .envelope-art { position: absolute; left: 736px; top: 3px; }
  .envelope-front { left: 776px; top: 150px; width: 372px; height: 166px; background: linear-gradient(170deg, #fff 40%, #eceef2); }
  .envelope-front .brand { font-size: 19px; top: 20px; left: 10px; }
  .envelope-front .address { top: 44px; left: 35px; }
  .envelope-front .web { bottom: 4px; left: 35px; letter-spacing: 1.5px; font-size: 6px; }
  .envelope-front .faint-circle { width: 48px; height: 48px; right: 3px; bottom: 6px; }

  /* Business cards */
  .card { width: 186px; height: 106px; top: 345px; }
  .card--front { left: 768px; }
  .card--back { left: 970px; background: var(--navy); box-shadow: none; }
  .card--front .brand { font-size: 17px; top: 12px; left: 7px; }
  .card--front .details { top: 52px; left: 7px; font-size: 5px; }
  .card--front .faint-circle { width: 38px; height: 38px; right: 6px; bottom: 6px; }
  .holder { position: absolute; right: 13px; top: 67px; text-align: center; }
  .holder-name { font-size: 7px; font-weight: 700; color: var(--navy); }
  .holder-title { font-size: 5px; color: #888; }
  .card--back .brand { color: #fff; font-size: 16px; top: 38px; left: 50%; transform: translateX(-50%); }
  .card--back .brand-dot { background: #fff; }
  .card--back .web { color: #fff; bottom: 10px; left: 0; right: 0; text-align: center; letter-spacing: 1.5px; font-size: 6px; }
</style>
</head>
<body>

  <!-- Letterhead, first option -->
  <section class="sheet letterhead letterhead--one" aria-label="Letterhead option one">
    <div class="faint-circle"></div>
    <div class="brand"><span class="brand-dot" style="width:14px;height:14px"></span>lumenreel</div>
    <p class="small footer-line">
      <span>Street Name, City Name, State Zip Code</span><span><b class="ico">&#9990;</b>123-456-0789</span><span><b class="ico">&#9993;</b>info@lumenreel.com</span><span><b class="ico">&#9679;</b>www.lumenreel.com</span>
    </p>
  </section>
  <div class="option-label" style="left:114px">Option-1</div>

  <!-- Letterhead, second option -->
  <section class="sheet letterhead letterhead--two" aria-label="Letterhead option two">
    <div class="faint-circle"></div>
    <div class="brand"><span class="brand-dot" style="width:14px;height:14px"></span>lumenreel</div>
    <p class="small address-block">Street Name, City Name<br>State Zip Code</p>
    <p class="small contact-stack">
      <b class="ico">&#9990;</b>123-456-0789<br>
      <b class="ico">&#9993;</b>info@lumenreel.com<br>
      <b class="ico">&#9679;</b>www.lumenreel.com
    </p>
  </section>
  <div class="option-label" style="left:479px">Option-2</div>

  <!-- Envelope backs -->
  <svg class="envelope-art" width="460" height="245" viewBox="0 0 460 245" aria-label="Envelope backs">
    <g transform="translate(82,1)">
      <rect width="374" height="124" fill="#fff"/>
      <path d="M0 0 H374 V14 Q370 26 350 32 L210 64 Q187 70 164 64 L24 32 Q4 26 0 14 Z" fill="var(--navy)"/>
      <circle cx="187" cy="36" r="10" fill="#fff"/>
    </g>
    <g transform="translate(1,73)">
      <rect width="372" height="165" fill="#fff" stroke="#ccc" stroke-width=".5"/>
      <path d="M0 1 H372 V8 Q368 22 348 28 L210 62 Q186 68 162 62 L24 28 Q4 22 2 8 Z" fill="#fff" stroke="#333" stroke-width="1"/>
      <circle cx="186" cy="42" r="10" fill="var(--navy)"/>
    </g>
  </svg>

  <!-- Envelope front -->
  <section class="sheet envelope-front" aria-label="Envelope front">
    <div class="faint-circle"></div>
    <div class="brand"><span class="brand-dot" style="width:13px;height:13px"></span>lumenreel</div>
    <p class="small address">Street Name, City Name, State Zip Code</p>
    <p class="small web">www.lumenreel.com</p>
  </section>

  <!-- Business card, front -->
  <section class="sheet card card--front" aria-label="Business card front">
    <div class="faint-circle"></div>
    <div class="brand"><span class="brand-dot" style="width:11px;height:11px"></span>lumenreel</div>
    <p class="small details">
      <b class="ico">&#9990;</b>123-456-0789<br>
      <b class="ico">&#9632;</b>123-456-0789<br>
      <b class="ico">&#9993;</b>info@lumenreel.com<br>
      <b class="ico">&#9679;</b>www.lumenreel.com<br>
      <span style="display:block;height:4px"></span>
      Street Name, City Name<br>State Zip Code
    </p>
    <div class="holder">
      <div class="holder-name">Your Name</div>
      <div class="holder-title">Title</div>
    </div>
  </section>

  <!-- Business card, back -->
  <section class="sheet card card--back" aria-label="Business card back">
    <div class="brand"><span class="brand-dot" style="width:11px;height:11px"></span>lumenreel</div>
    <p class="small web">www.lumenreel.com</p>
  </section>

</body>
</html>
```